Want to fly? Flight school needs a roll up

Hello designers

We are a small aviation club with around 100 members. We love flying and therefore offer free flight lessons for young people at our glider flight school.
The young people only have to pay a flat rate of €300 for the aircraft until their first solo flight.
To advertise the flight school we now need a roll up banner measuring 85cm x 200cm. You can find the data sheet for the banner in the appendix.
Content of the roll up banner:
Advertising for our flight school so that we can attract new members
The banner should be designed in our club colors blue/white
The banner is aimed at all people who want to get a glider license
A great offer for young people up to the age of 25 should be placed on the banner with a reference to the text “Offer only applies to people up to the age of 25. Included in the flat rate of €300 is training on the glider up to the first "solo flight"
The banner is intended to advertise training with a glider. Therefore the wish would be for a glider to be depicted

Here is a link to our current homepage

https://www.lgk-tarnholm.de/

https://www.vidoplex.example/watch?v=Qk7pL2xNz9c

Target Market(s)

Young people from 14 years to 30 years

Colors
0054AA
0677BA
7BADD7
CADEEF
E8F1F8

Requirements
Nice to have
• Glider / club logo
Should not have
• Too much text

```html
<!DOCTYPE html>
<html lang="en">
<head>
<meta charset="utf-8">
<title>Free Flight Lessons – Roll-up Banner</title>
<link rel="stylesheet" href="https://fonts.googleapis.com/css2?family=Poppins:ital,wght@0,600;0,700;1,800;1,900&family=Roboto:wght@700;900&family=Oswald:wght@500;600&display=swap">
<style>
  :root {
    --navy-deep: #03031f;
    --navy: #0b0b45;
    --royal: #1d1db0;
    --club-blue: #0054aa;
    --lavender: #9191f2;
    --sky-light: #cadeef;
    --sky-pale: #e8f1f8;
    --white: #ffffff;
    --ink: #1c1c2a;
    --black: #000000;
    --red: #e31b23;
  }
  html, body { margin: 0; padding: 0; overflow: hidden; background: var(--white); }
  .banner {
    position: relative;
    width: 1200px;
    height: 4000px;
    overflow: hidden;
    background: linear-gradient(180deg, var(--navy) 0%, var(--navy-deep) 45%, var(--navy) 100%);
    font-family: "Poppins", sans-serif;
  }
  .banner-shapes { position: absolute; inset: 0; }
  .club-badge {
    position: absolute;
    left: 420px; top: 150px;
    width: 360px; height: 360px;
    border-radius: 50%;
    background: var(--white);
    display: flex; flex-direction: column;
    align-items: center; justify-content: center;
    text-align: center;
  }
  .club-badge .dot {
    width: 46px; height: 46px; border-radius: 50%;
    background: var(--royal); margin-bottom: 22px;
  }
  .club-badge .club-name {
    font-family: "Poppins", sans-serif;
    font-weight: 700; font-size: 34px; line-height: 1.15;
    color: var(--royal);
  }
  .headline {
    position: absolute; left: 0; width: 1200px; top: 560px;
    text-align: center; margin: 0;
    font-family: "Poppins", sans-serif; font-style: italic; font-weight: 900;
    line-height: 1; letter-spacing: -2px;
  }
  .headline span { display: block; }
  .headline .free { font-size: 165px; color: var(--white); }
  .headline .flight { font-size: 225px; color: var(--lavender); margin-top: -6px; }
  .headline .lessons { font-size: 160px; color: var(--white); margin-top: -4px; }
  .age-note {
    position: absolute; left: 0; width: 1200px; top: 1195px;
    text-align: center; color: var(--white);
  }
  .age-note .small {
    font-family: "Oswald", sans-serif; font-weight: 500;
    font-size: 60px; letter-spacing: -1px; transform: scaleX(0.88); display: block;
  }
  .age-note .big {
    font-family: "Roboto", sans-serif; font-weight: 700;
    font-size: 160px; line-height: 1.05; display: block;
  }
  .photo { position: absolute; left: 0; width: 1200px; }
  .photo-glider {
    top: 1540px; height: 520px;
    background: linear-gradient(180deg, #1b22a8 0%, #3a52c9 35%, #aab3c4 55%, #1a2aa0 80%, #0c0c55 100%);
  }
  .photo-aircraft {
    top: 3020px; height: 980px;
    background: linear-gradient(180deg, #b9d3ea 0%, #3c4e8a 25%, #9b2a4a 45%, #6b6f84 60%, #3d5a2a 80%, #1f2a17 100%);
  }
  .training {
    position: absolute; left: 0; width: 1200px; top: 2370px;
    text-align: center; margin: 0;
  }
  .training .line {
    display: block; font-family: "Poppins", sans-serif; font-weight: 600;
    font-size: 62px; line-height: 1.2; color: var(--ink);
  }
  .training .solo {
    display: block; font-family: "Roboto", sans-serif; font-weight: 900;
    font-size: 96px; line-height: 1.15; color: var(--royal);
  }
  .price-strip {
    position: absolute; left: 85px; top: 2745px;
    width: 850px; height: 190px;
    background: var(--black);
    clip-path: polygon(60px 0, 100% 0, 100% 100%, 0 100%);
  }
  .price-strip p {
    margin: 0; position: absolute; left: 95px; top: 40px;
    font-family: "Poppins", sans-serif; font-style: italic; font-weight: 800;
    font-size: 62px; line-height: 1; color: var(--white);
  }
  .price-badge {
    position: absolute; left: 775px; top: 2690px; width: 300px; height: 300px;
  }
  .price-badge span {
    position: absolute; inset: 0; display: flex; align-items: center; justify-content: center;
    font-family: "Oswald", sans-serif; font-weight: 600; font-size: 112px; color: var(--white);
  }
  .web-address {
    position: absolute; left: 0; width: 1200px; top: 3800px; margin: 0;
    text-align: center; font-family: "Oswald", sans-serif; font-weight: 600;
    font-size: 100px; color: var(--white); letter-spacing: -1px;
  }
</style>
</head>
<body>
<main class="banner">
  <svg class="banner-shapes" width="1200" height="4000" viewBox="0 0 1200 4000" aria-hidden="true">
    <defs>
      <linearGradient id="lightPanel" x1="0" y1="0" x2="0" y2="1">
        <stop offset="0" stop-color="#ffffff"/>
        <stop offset="0.6" stop-color="#e8f1f8"/>
        <stop offset="1" stop-color="#cadeef"/>
      </linearGradient>
    </defs>
    <polygon points="0,0 1200,0 600,420" fill="#ffffff"/>
    <polygon points="0,0 40,0 600,392 600,420" fill="#1d1db0"/>
    <polygon points="1200,0 1160,0 600,392 600,420" fill="#1d1db0"/>
    <rect x="0" y="2060" width="1200" height="960" fill="url(#lightPanel)"/>
    <polygon points="0,2060 600,2060 0,2380" fill="#0b0b45"/>
    <polygon points="1200,2060 600,2060 1200,2380" fill="#0b0b45"/>
    <polygon points="430,2060 770,2060 600,2010" fill="#b9bcc6"/>
  </svg>

  <div class="club-badge">
    <div class="dot"></div>
    <div class="club-name">Luftsportgruppe<br>Tarnholm e.V.</div>
  </div>

  <h1 class="headline">
    <span class="free">FREE</span>
    <span class="flight">FLIGHT</span>
    <span class="lessons">LESSONS</span>
  </h1>

  <p class="age-note">
    <span class="small">OFFER ONLY APPLIES TO PEOPLE UP TO THE</span>
    <span class="big">AGE OF 25</span>
  </p>

  <div class="photo photo-glider" role="img" aria-label="Photo of a white glider in flight over a blue swoosh background"></div>

  <p class="training">
    <span class="line">IS TRAINING</span>
    <span class="line">ON THE GLIDER UP TO THE</span>
    <span class="solo">FIRST SOLO FLIGHT</span>
  </p>

  <div class="price-strip">
    <p>INCLUDED IN THE<br>FLAT RATE OF</p>
  </div>

  <div class="price-badge">
    <svg width="300" height="300" viewBox="0 0 300 300" aria-hidden="true">
      <g fill="#e31b23">
        <rect x="50" y="50" width="200" height="200" transform="rotate(0 150 150)"/>
        <rect x="50" y="50" width="200" height="200" transform="rotate(15 150 150)"/>
        <rect x="50" y="50" width="200" height="200" transform="rotate(30 150 150)"/>
        <rect x="50" y="50" width="200" height="200" transform="rotate(45 150 150)"/>
        <rect x="50" y="50" width="200" height="200" transform="rotate(60 150 150)"/>
        <rect x="50" y="50" width="200" height="200" transform="rotate(75 150 150)"/>
        <circle cx="150" cy="150" r="128"/>
      </g>
    </svg>
    <span>€300</span>
  </div>

  <div class="photo photo-aircraft" role="img" aria-label="Photo of red and white motor aircraft parked on a grass airfield"></div>

  <p class="web-address">www.lgk-tarnholm.de</p>
</main>
</body>
</html>
```